I have written a book called "Whispers from the Back Office - Uncover the trade tricks advisers bill huge fees every season for and would rather keep hidden"

This book will be sold through this webpage as an ebook. i have attached a copy of the cover of the book and I would like the website to be consistent with the look and feel of the book cover.

Target Market(s)

Business owners

Industry/Entity Type

Business

Requirements
Must have
• There has been a video produced for the promotion of this book which is yet to be completed. The video will be on ClipNest and the video needs to be prominent on the homepage.

I need to be able to manage and change the content as I wish on the website eg wordpress.

The page will need have a Coinvey purchase button

Also a 100% money back guarantee sign

Nice to have
• Friendloop plug in to show how many people like the page

Should not have
• I don't want the homepage or any of the other pages to be too cluttered

```html
<!DOCTYPE html>
<html lang="en">
<head>
<meta charset="utf-8">
<title>Whispers from the Back Office</title>
<link rel="stylesheet" href="https://fonts.googleapis.com/css2?family=Oswald:wght@300;400&family=Arimo:wght@400;700&display=swap">
<style>
:root{
  --brand-blue:#00aeef;
  --hero-blue:#00abeb;
  --button-blue:#0096d1;
  --ink:#111111;
  --nav-grey:#666666;
  --heading-grey:#7a7a7a;
  --body-grey:#8a8a8a;
  --panel-border:#d6d6d6;
  --panel-top:#f7f7f7;
  --panel-bottom:#e6e6e6;
  --footer-bg:#3c3c3c;
  --white:#ffffff;
  --seal-gold:#c9951f;
  --link-blue:#3b5998;
}
*{margin:0;padding:0;box-sizing:border-box}
html,body{width:1200px;height:970px;overflow:hidden;background:var(--white)}
body{position:relative;font-family:"Arimo",Arial,sans-serif}
.top-rule{position:absolute;left:0;top:0;width:1200px;height:6px;background:var(--brand-blue)}

.site-header{position:absolute;left:0;top:6px;width:1200px;height:133px}
.brand{position:absolute;left:119px;top:26px;font-family:"Oswald",sans-serif;line-height:1}
.brand-line-1{display:block;color:var(--brand-blue);font-size:44px;font-weight:400;letter-spacing:-0.5px}
.brand-line-2{display:block;color:var(--ink);font-size:31px;font-weight:400;margin-top:8px}
.main-nav{position:absolute;top:50px;left:649px;display:flex}
.main-nav a{font-family:"Oswald",sans-serif;font-size:15px;color:var(--nav-grey);text-decoration:none;font-weight:400;margin-right:40px}
.main-nav a:last-child{margin-right:0}

.hero{position:absolute;left:0;top:139px;width:1200px;height:431px;background:var(--hero-blue);overflow:hidden}
.hero-title{position:absolute;left:130px;top:82px;font-family:"Oswald",sans-serif;font-weight:400;font-size:44px;line-height:45px;color:var(--white);letter-spacing:-0.5px}
.hero-text{position:absolute;left:130px;top:198px;width:466px;font-family:"Oswald",sans-serif;font-weight:300;font-size:14.5px;line-height:22px;color:var(--white);text-transform:uppercase;text-align:justify}
.btn-learn{position:absolute;left:129px;top:307px;width:122px;height:45px;border-radius:10px;border:1px solid #bdbdbd;background:linear-gradient(#ffffff,#cfcfcf);box-shadow:0 1px 3px rgba(0,0,0,.35);font-family:"Oswald",sans-serif;font-size:18px;color:#777;display:flex;align-items:center;justify-content:center}
.slider-dots{position:absolute;left:130px;top:394px;display:flex;gap:5px}
.slider-dots span{width:10px;height:10px;border-radius:50%;background:radial-gradient(circle at 40% 35%,#bbb,#666)}
.slider-dots span.active{background:radial-gradient(circle at 40% 35%,#888,#222)}
.hero-art{position:absolute;left:653px;top:9px;width:378px;height:422px;background:linear-gradient(165deg,#f0f0f0 0%,#dcdcdc 45%,#2a2a2a 70%,#0a0a0a 100%);opacity:.9}

.welcome-heading{position:absolute;left:120px;top:585px;font-family:"Oswald",sans-serif;font-size:19px;color:var(--heading-grey);font-weight:400}
.promo-video{position:absolute;left:120px;top:630px;width:300px;height:247px;background:linear-gradient(135deg,#e8e6e3 0%,#d8d6d4 55%,#5dbde6 80%,#2a2a2a 100%)}
.welcome-copy{position:absolute;left:430px;top:628px;width:320px;font-size:11.3px;line-height:15.6px;color:var(--body-grey);text-align:justify}
.welcome-copy p{margin-bottom:15px}

.sidebar-panel{position:absolute;left:780px;width:300px;border:1px solid var(--panel-border)}
.guarantee{top:591px;height:71px;background:linear-gradient(var(--panel-top),var(--panel-bottom));display:flex;align-items:center}
.guarantee-seal{width:54px;height:54px;border-radius:50%;background:var(--seal-gold);margin-left:22px;flex:none}
.guarantee-label{font-family:"Oswald",sans-serif;font-size:19px;color:var(--heading-grey);margin-left:30px;white-space:nowrap}
.purchase{top:667px;height:71px;background:linear-gradient(var(--panel-top),var(--panel-bottom))}
.btn-buy{position:absolute;left:10px;top:14px;width:186px;height:42px;border-radius:6px;background:var(--button-blue);font-family:"Oswald",sans-serif;font-weight:400;font-size:20px;color:var(--white);display:flex;align-items:center;justify-content:center;letter-spacing:.5px}
.card-grid{position:absolute;left:204px;top:8px;width:84px;display:grid;grid-template-columns:40px 40px;gap:4px}
.card-grid span{height:25px;background:var(--white);border:1px solid #cfcfcf;font-family:"Arimo",sans-serif;font-size:7.5px;color:#555;display:flex;align-items:center;justify-content:center}
.social-widget{top:743px;height:133px;background:var(--white)}
.widget-mark{position:absolute;left:4px;top:4px;width:36px;height:36px;background:#4a6aa5}
.widget-title{position:absolute;left:48px;top:4px;font-size:12px;font-weight:700;color:var(--link-blue)}
.btn-like{position:absolute;left:48px;top:22px;width:42px;height:19px;border:1px solid #c5c5c5;background:#f2f2f2;font-size:9px;color:#333;display:flex;align-items:center;justify-content:center}
.widget-rule{position:absolute;left:4px;right:4px;top:50px;border-top:1px solid #ddd}
.like-count{position:absolute;left:5px;top:54px;font-size:9.5px;color:#333}
.like-count b{font-weight:700}
.fan-row{position:absolute;left:4px;top:69px;display:flex;gap:4px}
.fan{width:44px;text-align:center;font-size:8px;color:#666}
.fan-photo{width:44px;height:44px;background:linear-gradient(#d8d2cc,#5a5048);margin-bottom:6px}

.site-footer{position:absolute;left:0;top:908px;width:1200px;height:62px;background:var(--footer-bg)}
.copyright{position:absolute;left:121px;top:27px;font-size:12px;color:var(--white)}
.copyright .sep{margin:0 8px}
.social-links{position:absolute;right:122px;top:26px;display:flex;gap:12px;font-size:11px;color:var(--white)}
</style>
</head>
<body>
<div class="top-rule"></div>

<header class="site-header">
  <div class="brand">
    <span class="brand-line-1">WHISPERS FROM</span>
    <span class="brand-line-2">THE BACK OFFICE</span>
  </div>
  <nav class="main-nav">
    <a href="#">HOME</a>
    <a href="#">ABOUT US</a>
    <a href="#">ONLINE SALE</a>
    <a href="#">BUY NOW</a>
    <a href="#">CONTACT</a>
  </nav>
</header>

<section class="hero">
  <h1 class="hero-title">WHISPERS FROM<br>THE BACK OFFICE</h1>
  <p class="hero-text">Sed ut perspiciatis unde omnis iste natus error sit voluptatem accusantium doloremque laudantium, totam rem aperiam, eaque ipsa quae ab illo inventore veritatis et quasi architecto beatae vitae dicta sunt explicabo. Nemo enim</p>
  <div class="btn-learn">LEARN MORE</div>
  <div class="slider-dots"><span></span><span class="active"></span><span></span></div>
  <div class="hero-art" role="img" aria-label="Book cover artwork: folded white paper banner titled Whispers from the Back Office, with a silhouette of a man in a suit"></div>
</section>

<main>
  <h2 class="welcome-heading">WELCOME!</h2>
  <div class="promo-video" role="img" aria-label="Promotional ClipNest video: businesswoman beside the book covers, with a play button"></div>
  <div class="welcome-copy">
    <p>Sed ut perspiciatis unde omnis iste natus error sit voluptatem accusantium doloremque laudantium,</p>
    <p>totam rem aperiam, eaque ipsa quae ab illo inventore veritatis et quasi architecto beatae vitae dicta sunt explicabo. Nemo enim ipsam voluptatem quia voluptas sit aspernatur aut odit aut fugit, sed quia consequuntur magni dolores eos qui ratione voluptatem sequi nesciunt.</p>
    <p>Neque porro quisquam est, qui dolorem ipsum quia dolor sit amet, consectetur, adipisci velit, sed quia non numquam eius modi tempora incidunt ut labore et dolore magnam aliquam quaerat voluptatem. Ut enim ad minima veniam, quis nostrum exercitationem ullam corporis suscipit laboriosam, ut labore et dolore magnam aliquam quaerat voluptatem. Ut enim ad minima veniam, quis nostrum exercitat</p>
  </div>

  <aside>
    <div class="sidebar-panel guarantee">
      <div class="guarantee-seal"></div>
      <span class="guarantee-label">MONEY BACK GUARANTEE</span>
    </div>
    <div class="sidebar-panel purchase">
      <div class="btn-buy">Buy Now</div>
      <div class="card-grid">
        <span>Tallowpay</span><span>Brindlecard</span>
        <span>Quillon</span><span>Pennetto</span>
      </div>
    </div>
    <div class="sidebar-panel social-widget">
      <div class="widget-mark"></div>
      <div class="widget-title">Friendloop Platform</div>
      <div class="btn-like">Like</div>
      <div class="widget-rule"></div>
      <div class="like-count">1,988,819 people like <b>Friendloop Platform.</b></div>
      <div class="fan-row">
        <div class="fan"><div class="fan-photo" role="img" aria-label="Fan profile photo"></div>Levan</div>
        <div class="fan"><div class="fan-photo" role="img" aria-label="Fan profile photo"></div>Marta</div>
        <div class="fan"><div class="fan-photo" role="img" aria-label="Fan profile photo"></div>Tobias</div>
        <div class="fan"><div class="fan-photo" role="img" aria-label="Fan profile photo"></div>Karim</div>
        <div class="fan"><div class="fan-photo" role="img" aria-label="Fan profile photo"></div>Elsie</div>
      </div>
    </div>
  </aside>
</main>

<footer class="site-footer">
  <p class="copyright">Copyright 2013 © Whispers from the Back Office<span class="sep">|</span>Terms &amp; Conditions</p>
  <div class="social-links">
    <span>Friendloop</span><span>Chirpline</span><span>ClipNest</span><span>Coinvey</span><span>Feed</span>
  </div>
</footer>
</body>
</html>
```